Pine Ledge Traders, LLC- Global Beverage Company with 100% Cold Chain Logistics

Hey All, My Name is Dale, I am a young business owner in a competitive export space, but my niche is that I am shipping all of my beer around the world, "100% Cold Chain". This model is more costly, but it protects the integrity of the beer itself and will give folks in foreign countries the best representation of what US Craft Beer has to offer.

I am not a branding guy and don't claim to be one, I am a salesperson first, and will be referring to all of you to create something great that will be memorable.

I am looking for a basic Business Card Design for my Craft Beer Export company. I sell US Craft Beer in several countries around the globe. Austrailia, China, Taiwan, Chile, France, New Zealand... to name a few.

I am looking for a sleek, modern, and fresh design. Quickly!

Thanks for your consideration!

Cheers,

Dale

Target Market(s)

International

Contact Information for Business Card

Dale Corrigan
Founder- Roaming Hops Guy
Dale@PineLedgeTraders.example
@RoamingHopsGuy- Instagram only
www.Pineledgetraders.example
@PineLedgeTradersAU- Instagram Only

Font styles to use
Serif

Colors
0592cd
ffffff

Requirements
Must have
• Name-
• Title-
• Email-
• Social Media Handle-
• Company Website-
Nice to have
• Nice Logo/ Images on Card
Should not have
• Tacky Beer Images

```html
<!DOCTYPE html>
<html lang="en">
<head>
<meta charset="utf-8">
<title>Pine Ledge Traders – Business Card</title>
<link rel="stylesheet" href="https://fonts.googleapis.com/css2?family=Outfit:wght@600&family=Roboto:wght@400&display=swap">
<style>
  :root {
    --brand-blue: #0592cd;
    --white: #ffffff;
    --backdrop: #ececec;
    --ink: #3a3a3a;
    --rule-grey: #b5b5b5;
    --social-blue: #2f4f8f;
  }
  * { box-sizing: border-box; margin: 0; padding: 0; }
  html, body { width: 1000px; height: 1200px; overflow: hidden; }
  body { background: var(--backdrop); position: relative; font-family: "Roboto", sans-serif; }

  .card { position: absolute; left: 215px; width: 575px; height: 355px; overflow: hidden; }
  .card--front { top: 220px; background: var(--white); border-radius: 12px 75px 12px 75px; }
  .card--back { top: 607px; background: var(--brand-blue); border-radius: 75px 12px 75px 12px; }

  .lockup { position: absolute; display: flex; align-items: center; height: 70px; }
  .card--front .lockup { left: 33px; top: 47px; }
  .card--back .lockup { left: 100px; top: 142px; }

  .brand-mark { width: 62px; height: 62px; border-radius: 7px; flex: none; }
  .card--front .brand-mark { background: var(--brand-blue); }
  .card--back .brand-mark { background: var(--white); }

  .lockup__rule { width: 2px; height: 70px; margin: 0 16px 0 18px; flex: none; }
  .card--front .lockup__rule { background: var(--rule-grey); }
  .card--back .lockup__rule { background: var(--white); }

  .wordmark { font-family: "Outfit", sans-serif; font-weight: 600; font-size: 36px;
              line-height: 33px; letter-spacing: 0.3px; text-transform: uppercase; white-space: nowrap; }
  .card--front .wordmark { color: var(--brand-blue); }
  .card--back .wordmark { color: var(--white); }

  .contact { position: absolute; left: 207px; top: 150px; color: var(--ink); }
  .contact__name { font-family: "Outfit", sans-serif; font-weight: 600; font-size: 24px; color: var(--brand-blue); line-height: 30px; }
  .contact__title { font-size: 16px; line-height: 20px; }
  .contact__list { list-style: none; margin-top: 17px; font-size: 16px; }
  .contact__item { display: flex; align-items: center; gap: 7px; height: 22px; }
  .contact__item--social { margin-top: 21px; }
  .contact__icon { width: 15px; height: 15px; flex: none; }
  .social-square { width: 19px; height: 19px; background: var(--social-blue); border-radius: 2px; flex: none; }

  .world-map { position: absolute; left: 0; top: 30px; width: 560px; height: 235px;
               border-radius: 30px 60px 40px 20px;
               background: linear-gradient(180deg, rgba(255,255,255,0.13) 0%, rgba(255,255,255,0.09) 60%, rgba(255,255,255,0.03) 100%); }

  .markets { position: absolute; left: 0; right: 0; top: 268px; text-align: center;
             color: var(--white); font-size: 16.5px; letter-spacing: 0.1px; white-space: nowrap; }
</style>
</head>
<body>
  <section class="card card--front">
    <div class="lockup">
      <div class="brand-mark"></div>
      <div class="lockup__rule"></div>
      <div class="wordmark">Pine Ledge<br>Traders</div>
    </div>
    <div class="contact">
      <p class="contact__name">Dale Corrigan</p>
      <p class="contact__title">Founder - Roaming Hops Guy</p>
      <ul class="contact__list">
        <li class="contact__item">
          <svg class="contact__icon" viewBox="0 0 16 16"><rect x="1" y="3" width="14" height="10" fill="none" stroke="#0592cd" stroke-width="1.6"/><path d="M1 3 L8 9 L15 3" fill="none" stroke="#0592cd" stroke-width="1.6"/></svg>
          Dale@PineLedgeTraders.example
        </li>
        <li class="contact__item">
          <svg class="contact__icon" viewBox="0 0 16 16"><circle cx="8" cy="8" r="7" fill="#0592cd"/><ellipse cx="8" cy="8" rx="3" ry="6" fill="none" stroke="#fff" stroke-width="1.1"/><path d="M2 8 H14" stroke="#fff" stroke-width="1.1"/></svg>
          www.Pineledgetraders.example
        </li>
        <li class="contact__item contact__item--social">
          <span class="social-square"></span>
          @RoamingHopsGuy
        </li>
      </ul>
    </div>
  </section>

  <section class="card card--back">
    <div class="world-map" role="img" aria-label="Dotted world map background"></div>
    <div class="lockup">
      <div class="brand-mark"></div>
      <div class="lockup__rule"></div>
      <div class="wordmark">Pine Ledge<br>Traders</div>
    </div>
    <p class="markets">AUSTRAILIA | CHINA | TAIWAN | CHILE | FRANCE | NEW ZEALAND</p>
  </section>
</body>
</html>
```